Veterinary Hospital Business Card

We have recently updated our logo and wish to have a business card designed incorporating the new look and flow. We are a full service veterinary hospital also offering laser therapy, boarding, and grooming. Our website is www.marlowpawsvets.com

Industry/Entity Type

Veterinary

```html
<!DOCTYPE html>
<html lang="en">
<head>
<meta charset="utf-8">
<title>Marlow Paws Animal Hospital – Business Card</title>
<link rel="stylesheet" href="https://fonts.googleapis.com/css2?family=Exo+2:wght@300;400;600&display=swap">
<style>
  :root {
    --backdrop: #ebe7e0;
    --card: #ffffff;
    --band: #4a7d99;
    --navy: #1f4f6e;
    --sky: #6fa6c6;
    --ink: #3d4a55;
    --muted: #6b7780;
  }
  * { box-sizing: border-box; margin: 0; padding: 0; }
  html, body {
    width: 1071px; height: 1200px; overflow: hidden;
    background: var(--backdrop);
    font-family: "Exo 2", sans-serif;
  }
  .sheet {
    width: 1071px; height: 1200px;
    display: flex; flex-direction: column; align-items: center; justify-content: center;
    gap: 70px;
  }
  .card {
    position: relative;
    width: 840px; height: 480px;
    background: var(--card);
    box-shadow: 0 10px 28px rgba(0,0,0,.14);
    overflow: hidden;
  }

  /* contact side */
  .identity { position: absolute; left: 0; top: 70px; display: flex; align-items: flex-start; }
  .identity-marker { width: 34px; height: 34px; background: var(--band); margin-right: 22px; }
  .person-name { font-size: 34px; font-weight: 300; color: var(--band); letter-spacing: 1px; line-height: 1; }
  .person-role { font-size: 17px; font-weight: 400; color: var(--ink); letter-spacing: 2px; margin-top: 8px; }

  .contacts { position: absolute; left: 56px; top: 170px; list-style: none; }
  .contacts li { display: flex; align-items: center; gap: 14px; font-size: 16px; color: var(--muted); height: 30px; letter-spacing: .5px; }
  .contacts svg { width: 16px; height: 16px; fill: var(--band); }

  .address-band {
    position: absolute; left: 0; right: 0; bottom: 0; height: 128px;
    background: var(--band);
    padding: 30px 56px;
    color: #e6f0f6; font-size: 19px; letter-spacing: 1px; line-height: 1.55;
  }

  .brand {
    position: absolute; display: flex; align-items: center; gap: 14px;
  }
  .brand-dot { width: 22px; height: 22px; border-radius: 50%; background: var(--sky); flex: none; }
  .brand-name {
    font-weight: 600; color: var(--navy); text-transform: uppercase;
    line-height: 1; letter-spacing: 1px;
  }
  .card-contact .brand { right: 48px; top: 118px; }
  .card-contact .brand-name { font-size: 34px; text-align: right; }

  /* logo side */
  .card-logo .brand { left: 50%; top: 50%; transform: translate(-50%, -50%); }
  .card-logo .brand-name { font-size: 52px; }
  .edge-stripe { position: absolute; left: 0; right: 0; bottom: 0; height: 12px; background: var(--sky); }
</style>
</head>
<body>
<main class="sheet">

  <section class="card card-contact" aria-label="Business card, contact side">
    <div class="identity">
      <span class="identity-marker"></span>
      <div>
        <p class="person-name">DANIEL HART</p>
        <p class="person-role">GENERAL MANAGER</p>
      </div>
    </div>

    <ul class="contacts">
      <li>
        <svg viewBox="0 0 16 16"><path d="M3.5 1.5l2.5 0 1 3.5-1.6 1.2a8 8 0 0 0 4.4 4.4L11 9l3.5 1v2.5c0 1-1 2-2 2A11 11 0 0 1 1.5 3.5c0-1 1-2 2-2z"/></svg>
        012 555 0147
      </li>
      <li>
        <svg viewBox="0 0 16 16"><path d="M2 2h12v12H2z M4 4v8h8V4z"/></svg>
        012 555 0148
      </li>
      <li>
        <svg viewBox="0 0 16 16"><path d="M4 1h8v4H4z M2 6h12v6h-2v3H4v-3H2z M5 10v4h6v-4z"/></svg>
        012 555 0149
      </li>
      <li>
        <svg viewBox="0 0 16 16"><path d="M1 3h14v10H1z M2.5 4.5 8 9l5.5-4.5z"/></svg>
        hello@marlowpawsvets.com
      </li>
      <li>
        <svg viewBox="0 0 16 16"><circle cx="8" cy="8" r="7"/></svg>
        www.marlowpawsvets.com
      </li>
    </ul>

    <div class="brand">
      <p class="brand-name">Marlow Paws<br>Animal Hospital</p>
      <span class="brand-dot"></span>
    </div>

    <div class="address-band">
      <p>42 Alder Grove Road,</p>
      <p>2nd Floor Suite B</p>
    </div>
  </section>

  <section class="card card-logo" aria-label="Business card, logo side">
    <div class="brand">
      <span class="brand-dot"></span>
      <p class="brand-name">Marlow Paws<br>Animal Hospital</p>
    </div>
    <div class="edge-stripe"></div>
  </section>

</main>
</body>
</html>
```